Timber Crest Construction Needs business card

Hey we are in need of business card designs. I have upload our logo as a guideline, but free feel to run with it or come up with something unique.
Pls have fun with it and be creative. the name says it all!
i will give some directions after i see a few entries..
Updates
Logo source file has been uploaded..
Hey because of the logo is so colourful already.
Can we have a few submissions with less colour.
Also we are looking for clever/hidden/descriptive business card.

```html
<!DOCTYPE html>
<html lang="en">
<head>
<meta charset="utf-8">
<title>Timber Crest Construction – Business Card</title>
<link href="https://fonts.googleapis.com/css2?family=Oswald:wght@400;500;600&family=Roboto:wght@400;500&display=swap" rel="stylesheet">
<style>
  :root {
    --stage: #ecebe8;
    --paper: #ffffff;
    --frame-grey: #8c8c8c;
    --brand-yellow: #f6c21c;
    --brand-blue: #1e9bd1;
    --ink-grey: #8f8f8f;
    --ink-dark: #2f2f2f;
    --icon-dark: #333333;
  }
  * { box-sizing: border-box; margin: 0; padding: 0; }
  html, body { width: 1076px; height: 1200px; overflow: hidden; }
  body {
    background: var(--stage);
    font-family: "Roboto", Arial, sans-serif;
    position: relative;
  }
  .card {
    position: absolute;
    left: 158px;
    width: 760px;
    height: 434px;
    background: var(--paper);
    box-shadow: 0 6px 22px rgba(0,0,0,0.18);
    overflow: hidden;
  }
  /* Front */
  .card--front { top: 60px; background: var(--frame-grey); padding: 16px; }
  .front-frame { width: 100%; height: 100%; background: var(--brand-yellow); padding: 11px; }
  .front-field {
    width: 100%; height: 100%; background: var(--paper);
    display: flex; align-items: center; justify-content: center;
  }
  .wordmark { display: flex; align-items: center; gap: 14px; }
  .wordmark__square { width: 34px; height: 34px; background: var(--brand-yellow); flex: none; }
  .wordmark__name {
    font-family: "Oswald", Arial, sans-serif; font-weight: 500;
    color: var(--ink-grey); text-transform: uppercase; line-height: 1;
  }
  .card--front .wordmark__name { font-size: 44px; }
  .wordmark__name small { display: block; font-size: 0.42em; letter-spacing: 0.32em; margin-top: 6px; }

  /* Back */
  .card--back { top: 640px; }
  .back-logo { position: absolute; left: 60px; top: 92px; }
  .card--back .wordmark__name { font-size: 40px; }
  .name-block {
    position: absolute; left: 240px; top: 290px; width: 270px; height: 102px;
    background: var(--brand-blue); color: var(--paper);
    padding: 20px 24px;
  }
  .name-block__name { font-family: "Oswald", Arial, sans-serif; font-weight: 600; font-size: 34px; letter-spacing: 1px; line-height: 1; }
  .name-block__role { font-size: 13px; letter-spacing: 2px; margin-top: 8px; text-transform: uppercase; }
  .base-strip { position: absolute; left: 240px; top: 392px; width: 520px; height: 20px; background: var(--frame-grey); }
  .contact-list { position: absolute; left: 440px; top: 182px; width: 320px; list-style: none; }
  .contact-row {
    height: 36px; display: flex; align-items: center; justify-content: space-between;
    padding-left: 22px; font-size: 11.5px; color: var(--ink-dark); line-height: 1.25;
  }
  .contact-row--yellow { background: var(--brand-yellow); }
  .contact-row--blue { background: var(--brand-blue); color: var(--paper); }
  .contact-icon {
    width: 24px; height: 24px; background: var(--icon-dark); margin-right: 12px;
    display: flex; align-items: center; justify-content: center;
  }
</style>
</head>
<body>
  <section class="card card--front" aria-label="Business card front">
    <div class="front-frame">
      <div class="front-field">
        <div class="wordmark">
          <span class="wordmark__square"></span>
          <span class="wordmark__name">Timber Crest<small>Construction</small></span>
        </div>
      </div>
    </div>
  </section>

  <section class="card card--back" aria-label="Business card back">
    <div class="wordmark back-logo">
      <span class="wordmark__square"></span>
      <span class="wordmark__name">Timber Crest<small>Construction</small></span>
    </div>

    <ul class="contact-list">
      <li class="contact-row contact-row--yellow">
        <span>012 555 0182<br>012 555 0194</span>
        <span class="contact-icon">
          <svg width="14" height="14" viewBox="0 0 24 24"><path fill="#fff" d="M6.6 10.8a15.1 15.1 0 0 0 6.6 6.6l2.2-2.2a1 1 0 0 1 1-.25 11.4 11.4 0 0 0 3.6.57 1 1 0 0 1 1 1V20a1 1 0 0 1-1 1A17 17 0 0 1 3 4a1 1 0 0 1 1-1h3.5a1 1 0 0 1 1 1c0 1.25.2 2.45.57 3.57a1 1 0 0 1-.25 1z"/></svg>
        </span>
      </li>
      <li class="contact-row contact-row--blue">
        <span>mail@timbercrest.com<br>www.timbercrest.com</span>
        <span class="contact-icon">
          <svg width="14" height="14" viewBox="0 0 24 24" fill="none" stroke="#fff" stroke-width="2"><circle cx="12" cy="12" r="9"/><path d="M3 12h18M12 3c3 3 3 15 0 18M12 3c-3 3-3 15 0 18"/></svg>
        </span>
      </li>
      <li class="contact-row contact-row--yellow">
        <span>188 Cedar Ridge Road<br>Hill Valley, NY 10021</span>
        <span class="contact-icon">
          <svg width="14" height="14" viewBox="0 0 24 24"><path fill="#fff" d="M12 2a7 7 0 0 0-7 7c0 5 7 13 7 13s7-8 7-13a7 7 0 0 0-7-7zm0 9.5A2.5 2.5 0 1 1 12 6.5a2.5 2.5 0 0 1 0 5z"/></svg>
        </span>
      </li>
    </ul>

    <div class="name-block">
      <p class="name-block__name">AARON PIKE</p>
      <p class="name-block__role">General Manager</p>
    </div>
    <div class="base-strip"></div>
  </section>
</body>
</html>
```